eCommerce Website Design for Children's Book Service

I am looking for a 5 page eCommerce website that includes a Shopping Cart. 'Lumiva Books' is the title of the company and its logo is attached. 'Sprouting wonder in words,' is the company's motto and 'spring green' is the main color. The website needs to appeal to families. Images of books and/or maple seeds (helicopter seeds) moving are part of the graphics.
Updates

I have updated my brief and I would like my website design to include 5 pages: home, about, products (books), blog, contact. WordPress is the web format that I am most comfortable with.

Target Market(s)

Families with young children

Coding

Coded - Design and coding required

Number of Pages Required

5+ page

Requirements
Must have
• Shopping cart page; contact page, books page with spaces of photos to go, blog page; spring green color
Nice to have
• A graphic that relates to motto : "sprouting wonder in words"
• WordPress

```html
<!DOCTYPE html>
<html lang="en">
<head>
<meta charset="utf-8">
<title>Lumiva Books — Sprouting wonder in words</title>
<link href="https://fonts.googleapis.com/css2?family=Mulish:ital,wght@0,400;0,600;0,700;0,800;1,400&display=swap" rel="stylesheet">
<style>
:root{
  --green:#3b8f2f;
  --green-dark:#2f7a25;
  --ink:#1e1e1e;
  --text:#444;
  --muted:#777;
  --red:#e0342c;
  --band:#efefef;
  --footer:#2a2a2a;
  --white:#fff;
}
*{margin:0;padding:0;box-sizing:border-box}
html,body{width:1200px;height:4100px;overflow:hidden}
body{position:relative;background:var(--white);font-family:"Mulish",sans-serif;color:var(--ink)}
.abs{position:absolute}

/* Header / hero */
.hero-photo{left:0;top:0;width:1200px;height:700px;
  background:linear-gradient(100deg,#f6f6f4 0%,#f1ece7 40%,#f3d9c7 62%,#e9e4de 85%,#dcdcd8 100%)}
.hero-curve{left:0;top:590px;width:1200px;height:110px}
.brand{left:90px;top:60px;display:flex;align-items:center;gap:12px}
.brand-mark{width:22px;height:22px;background:var(--green);border-radius:50%}
.brand-name{font-size:30px;font-weight:700;color:var(--green);letter-spacing:.5px}
.topbar{right:90px;top:36px;display:flex;gap:48px;font-size:17px;font-weight:600;align-items:center}
.topbar span{display:flex;align-items:center;gap:10px}
.nav{right:92px;top:96px;display:flex;gap:48px;font-size:16px;font-weight:700;letter-spacing:.3px}
.hero-title{left:90px;top:285px;font-size:62px;font-weight:700;letter-spacing:1px}
.hero-sub{left:92px;top:346px;font-size:35px;font-weight:400;color:#333}
.btn{display:inline-flex;align-items:center;justify-content:center;background:var(--green);color:var(--white);border-radius:30px;font-weight:600}
.hero-btn{left:90px;top:432px;width:154px;height:50px;font-size:20px}
.dots{left:538px;top:562px;display:flex;gap:17px}
.dots i{width:18px;height:18px;border-radius:50%;border:2.5px solid #333;display:block}
.dots i.on{background:#333}

/* Section headings */
.section-title{left:0;width:1200px;text-align:center;font-size:50px;font-weight:600}
.seed{width:100px;height:64px;border-radius:40px 40px 40px 10px;background:linear-gradient(135deg,#7fc06a,#3b8f2f);opacity:.75}

/* About */
.about-text{left:219px;top:902px;width:762px;text-align:center;font-size:20px;line-height:33px;color:var(--text)}
.about-btn{left:514px;top:1107px;width:172px;height:50px;font-size:20px}

/* Products carousel */
.products-band{left:0;top:1285px;width:1200px;height:710px;background:var(--band)}
.ring{width:312px;height:312px;border-radius:50%;border:6px solid var(--green);background:var(--white);display:flex;flex-direction:column;align-items:center;justify-content:center}
.ring.active{background:var(--green)}
.cover{width:128px;height:190px}
.ring .price{font-size:24px;font-weight:700;color:var(--green);margin-top:14px}
.ring.active .price{color:var(--white)}
.ring .cover-wrap{position:relative}
.ring .shop{position:absolute;left:0;right:0;top:80px;margin:auto;width:128px;height:36px;border:2px solid var(--white);background:var(--green);color:var(--white);font-size:15px;font-weight:800;display:flex;align-items:center;justify-content:center}
.arrow{top:1685px;width:20px;height:30px}

/* Featured */
.card{top:2233px;width:236px;height:314px;border:5px solid #e8e8e8;background:#fff;padding:14px}
.card .cover{width:100%;height:100%}
.pname{top:2565px;width:236px;text-align:center;font-size:21px;font-weight:700}
.pprice{top:2598px;width:236px;text-align:center;font-size:19px;color:var(--red)}

/* Perks band */
.perks{left:0;top:2747px;width:1200px;height:177px;background:var(--green);color:var(--white)}
.perk{top:70px;display:flex;gap:14px;font-size:16px;font-weight:600;line-height:22px}
.perk svg{flex:none;margin-top:3px}

/* Testimonials */
.quote-mark{font-size:110px;color:#bbb;font-weight:800;line-height:1}
.testimonial{left:190px;top:3150px;width:820px;text-align:center;font-size:16px;font-style:italic;line-height:30px;color:var(--muted)}
.avatar{left:550px;top:3243px;width:100px;height:100px;border-radius:50%;border:5px solid var(--green);background:radial-gradient(circle,#c9a58a,#7a5e4c)}
.reviewer{left:0;top:3363px;width:1200px;text-align:center;font-size:15px;color:#333}

/* Footer */
.footer-bg{left:0;top:3470px;width:1200px;height:630px;background:linear-gradient(180deg,#2e2e2e,#242424 60%,#1c1c1c)}
.footer-curve{left:0;top:3420px;width:1200px;height:80px}
.news-title{left:123px;top:3603px;font-size:31px;font-weight:700;color:var(--white)}
.news-input{left:536px;top:3600px;width:404px;height:46px;background:var(--white);font-size:13px;font-style:italic;color:#999;padding:15px 18px}
.news-btn{left:940px;top:3600px;width:135px;height:46px;background:var(--green);color:var(--white);font-size:17px;font-weight:700;display:flex;align-items:center;justify-content:center}
.col{top:3762px;color:#ddd;font-size:14px;line-height:27px}
.col h4{font-size:15px;font-weight:700;color:var(--white);margin-bottom:13px;letter-spacing:.3px}
.social{left:506px;top:3974px;display:flex;gap:12px}
.social i{width:38px;height:38px;border-radius:50%;background:var(--green);display:block}
.copy{left:0;top:4052px;width:1200px;text-align:center;font-size:13px;color:#ddd}
</style>
</head>
<body>

<!-- Hero -->
<div class="abs hero-photo" role="img" aria-label="Smiling young girl reading an open book in a bright room"></div>
<svg class="abs hero-curve" viewBox="0 0 1200 110" aria-hidden="true">
  <path d="M0,30 C330,30 470,92 600,92 C730,92 870,30 1200,30 L1200,110 L0,110 Z" fill="#fff"/>
  <path d="M0,44 C330,44 470,104 600,104 C730,104 870,44 1200,44" fill="none" stroke="#3b8f2f" stroke-width="7"/>
</svg>

<div class="abs brand"><i class="brand-mark"></i><span class="brand-name">Lumiva Books</span></div>

<div class="abs topbar">
  <span><svg width="18" height="18" viewBox="0 0 24 24"><path d="M6.6 10.8a15 15 0 0 0 6.6 6.6l2.2-2.2a1 1 0 0 1 1-.25 11.4 11.4 0 0 0 3.6.57 1 1 0 0 1 1 1V20a1 1 0 0 1-1 1A17 17 0 0 1 3 4a1 1 0 0 1 1-1h3.5a1 1 0 0 1 1 1c0 1.25.2 2.45.57 3.57a1 1 0 0 1-.25 1z" fill="#1e1e1e"/></svg>1 555 010 745</span>
  <span style="font-size:14px"><svg width="20" height="18" viewBox="0 0 24 22"><path d="M1 1h4l2.7 12.4h12L23 5H7" fill="none" stroke="#1e1e1e" stroke-width="2.4"/><circle cx="9" cy="18.5" r="2" fill="#1e1e1e"/><circle cx="19" cy="18.5" r="2" fill="#1e1e1e"/></svg>Add To Cart</span>
</div>

<nav class="abs nav"><span>HOME</span><span>ABOUT US</span><span>CATEGORIES</span><span>PRODUCTS</span><span>SHOP</span><span>CONTACT US</span></nav>

<h1 class="abs hero-title">LUMIVA BOOKS</h1>
<p class="abs hero-sub">Sprouting wonder in words</p>
<a class="abs btn hero-btn">Shop Now</a>
<div class="abs dots"><i class="on"></i><i></i><i></i><i></i></div>

<!-- About -->
<div class="abs seed" style="left:640px;top:785px;width:85px;height:55px" role="img" aria-label="Flying maple seeds ornament"></div>
<h2 class="abs section-title" style="top:812px">About Us</h2>
<p class="abs about-text">Lorem ipsum dolor sit amet, consectetur adipiscing elit, sed do eiusmod tempor incididunt ut labore et dolore magna aliqua. Ut enim ad minim veniam, quis nostrud exercitation ullamco laboris nisi ut aliquip ex ea commodo consequat. Duis aute irure dolor in reprehenderit in voluptate velit esse cillum dolore eu fugiat nulla pariatur. Excepteur sint occaecat cupidatat non proident, sunt in culpa qui officia deserunt mollit anim id est laborum</p>
<a class="abs btn about-btn">Read More</a>

<!-- Our Products -->
<div class="abs products-band"></div>
<div class="abs seed" style="left:690px;top:1390px" role="img" aria-label="Flying maple seeds ornament"></div>
<h2 class="abs section-title" style="top:1443px">Our Products</h2>

<svg class="abs arrow" style="left:34px" viewBox="0 0 20 30" aria-hidden="true"><path d="M15 4 L5 15 L15 26" fill="none" stroke="#333" stroke-width="4"/></svg>
<svg class="abs arrow" style="left:1146px" viewBox="0 0 20 30" aria-hidden="true"><path d="M5 4 L15 15 L5 26" fill="none" stroke="#333" stroke-width="4"/></svg>

<div class="abs ring active" style="left:93px;top:1544px">
  <div class="cover-wrap"><div class="cover" role="img" aria-label="Children's book cover" style="background:linear-gradient(180deg,#8fc9a0,#4f9d6a)"></div><span class="shop">SHOP NOW</span></div>
  <span class="price">$14.00</span>
</div>
<div class="abs ring" style="left:443px;top:1544px">
  <div class="cover" role="img" aria-label="Back to school book cover with a school bus" style="background:linear-gradient(180deg,#cfe6f5,#f4d35e 55%,#7cb35a)"></div>
  <span class="price">$14.00</span>
</div>
<div class="abs ring" style="left:795px;top:1544px">
  <div class="cover" role="img" aria-label="Comic book cover" style="background:linear-gradient(180deg,#f7f2d0,#f3c43a 70%,#e35b2a)"></div>
  <span class="price">$14.00</span>
</div>

<!-- Featured Products -->
<div class="abs seed" style="left:755px;top:2080px" role="img" aria-label="Flying maple seeds ornament"></div>
<h2 class="abs section-title" style="top:2132px">Featured Products</h2>

<div class="abs card" style="left:101px"><div class="cover" role="img" aria-label="Superhero comic magazine cover" style="background:linear-gradient(180deg,#e8473a 0%,#3a78c2 35%,#2f5fa0 100%)"></div></div>
<div class="abs card" style="left:355px"><div class="cover" role="img" aria-label="Sci-fi comics cover with a rocket" style="background:linear-gradient(180deg,#f3d34a 0%,#d83a2e 35%,#a8271f 100%)"></div></div>
<div class="abs card" style="left:609px"><div class="cover" role="img" aria-label="Comics magazine cover" style="background:linear-gradient(180deg,#e8473a 0%,#f0c83c 30%,#2e6fa8 100%)"></div></div>
<div class="abs card" style="left:864px"><div class="cover" role="img" aria-label="Awesome comics cover" style="background:linear-gradient(180deg,#e03a2f 0%,#f7ecb0 30%,#f3d056 100%)"></div></div>

<div class="abs pname" style="left:101px">PRODUCT NAME</div><div class="abs pprice" style="left:101px">$29.00</div>
<div class="abs pname" style="left:355px">PRODUCT NAME</div><div class="abs pprice" style="left:355px">$19.00</div>
<div class="abs pname" style="left:609px">PRODUCT NAME</div><div class="abs pprice" style="left:609px">$99.00</div>
<div class="abs pname" style="left:864px">PRODUCT NAME</div><div class="abs pprice" style="left:864px">$59.00</div>

<!-- Perks -->
<section class="abs perks">
  <div class="abs perk" style="left:90px"><svg width="26" height="26" viewBox="0 0 24 24"><path d="M20 8a8 8 0 0 0-15-1M4 16a8 8 0 0 0 15 1" fill="none" stroke="#fff" stroke-width="2.6"/><path d="M20 3v5h-5M4 21v-5h5" fill="none" stroke="#fff" stroke-width="2.6"/></svg><div>90 days return<br>3 days for free return</div></div>
  <div class="abs perk" style="left:354px"><svg width="30" height="24" viewBox="0 0 30 24"><rect x="1" y="4" width="17" height="13" fill="#fff"/><path d="M18 8h6l4 5v4H18z" fill="#fff"/><circle cx="7" cy="19" r="3" fill="#fff" stroke="#3b8f2f" stroke-width="1.5"/><circle cx="23" cy="19" r="3" fill="#fff" stroke="#3b8f2f" stroke-width="1.5"/></svg><div>Free Shipping<br>Free shipping on order</div></div>
  <div class="abs perk" style="left:636px"><svg width="26" height="26" viewBox="0 0 24 24"><path d="M23 1 1 10l8 3 2 9 4-6 5 4z" fill="#fff"/></svg><div>Proffesional Support<br>Call : +1 555 010 254</div></div>
  <div class="abs perk" style="left:897px"><svg width="24" height="26" viewBox="0 0 24 26"><rect x="2" y="9" width="20" height="6" fill="#fff"/><rect x="4" y="15" width="16" height="10" fill="#fff"/><rect x="11" y="9" width="2" height="16" fill="#3b8f2f"/><path d="M12 9C9 2 4 4 7 8M12 9c3-7 8-5 5-1" fill="none" stroke="#fff" stroke-width="2"/></svg><div>Gift Card<br>Gift Card On Purchase</div></div>
</section>

<!-- Testimonials -->
<div class="abs seed" style="left:700px;top:3018px" role="img" aria-label="Flying maple seeds ornament"></div>
<h2 class="abs section-title" style="top:3068px">Testimonials</h2>
<div class="abs quote-mark" style="left:76px;top:3140px">&#8220;</div>
<div class="abs quote-mark" style="left:1084px;top:3140px">&#8221;</div>
<p class="abs testimonial">Sed ut perspiciatis unde omnis iste natus error sit voluptatem accusantium doloremque laudantium, totam rem aperiam, eaque ipsa quae ab illo inventore veritatis et quasi architecto beatae vitae dicta sunt explicabo.</p>
<div class="abs avatar" role="img" aria-label="Portrait of a reviewer"></div>
<p class="abs reviewer">- NORA FIELDS</p>

<!-- Footer -->
<div class="abs footer-bg" role="img" aria-label="Dimmed photo of a family reading together"></div>
<svg class="abs footer-curve" viewBox="0 0 1200 80" aria-hidden="true">
  <path d="M0,58 C360,58 500,14 600,14 C700,14 840,58 1200,58 L1200,80 L0,80 Z" fill="#2e2e2e"/>
  <path d="M0,44 C360,44 500,2 600,2 C700,2 840,44 1200,44" fill="none" stroke="#3b8f2f" stroke-width="7"/>
</svg>

<h3 class="abs news-title">Subscribe Our Newsletter</h3>
<div class="abs news-input">Enter Your Email Id</div>
<div class="abs news-btn">Subscribe</div>

<div class="abs col" style="left:120px"><h4>QUICK LINKS</h4>Home<br>About us<br>Categories<br>Products<br>Shop<br>Contact Us</div>
<div class="abs col" style="left:372px"><h4>OTHER LINKS</h4>Group Rate Form<br>Teacher's Guide<br>Gift Certificates<br>FAQs</div>
<div class="abs col" style="left:626px"><h4>CONTACT US</h4>PO Box 1020, Maple Glen, MI 48000<br>(555) 010-6549<br>hello@lumivabooks.com</div>
<div class="abs col" style="left:995px"><h4>ACCOUNT</h4>Sign Up<br>My Account</div>

<div class="abs social" aria-label="Social links"><i></i><i></i><i></i><i></i></div>
<p class="abs copy">&copy; Copyrights 2019 The Company Name All Rights Reserved</p>

</body>
</html>
```